VKT Consulting

Government/Entitlement Consulting Services- I assist developers obtain entitlements from local, state and federal government agencies so that they can build their projects. Often these projects are very complicated and political and may face community opposition.

Target Market(s)

Real Estate Developers

Industry/Entity Type

Business Consultant

Contact Information for Business Card

Dana Melbrook
Principal

Font styles to use
Serif
Sans Serif

Requirements
Must have
• Classy and professional appeal.
Nice to have
• I like a combination of a mat and glossy finish. I've seen that done with black and then a bold color for a pop, but am not 100% committed to that.

```html
<!DOCTYPE html>
<html lang="en">
<head>
<meta charset="utf-8">
<title>VKT Consulting – Business Card</title>
<link rel="stylesheet" href="https://fonts.googleapis.com/css2?family=Open+Sans:wght@400;700&display=swap">
<style>
  :root {
    --backdrop: #e9e6e1;
    --card-black: #111111;
    --card-white: #ffffff;
    --brand-red: #b50d12;
    --ink: #3a3a3a;
    --ink-soft: #555555;
    --shadow: rgba(0, 0, 0, 0.22);
  }
  html, body {
    margin: 0;
    padding: 0;
    overflow: hidden;
  }
  .canvas {
    position: relative;
    width: 1200px;
    height: 900px;
    background: var(--backdrop);
    overflow: hidden;
    font-family: "Open Sans", Arial, sans-serif;
  }
  .card {
    position: absolute;
    width: 560px;
    height: 320px;
    box-shadow: 0 10px 24px var(--shadow);
    overflow: hidden;
  }
  .card-front {
    left: 570px;
    top: 90px;
    background: var(--card-black);
  }
  .card-back {
    left: 70px;
    top: 470px;
    background: var(--card-white);
  }
  .wordmark {
    position: absolute;
    font-family: "Open Sans", Arial, sans-serif;
    font-weight: 400;
    font-size: 44px;
    letter-spacing: 3px;
    white-space: nowrap;
    display: flex;
    align-items: center;
    gap: 14px;
  }
  .wordmark .mark-dot {
    width: 14px;
    height: 14px;
    border-radius: 50%;
  }
  .card-front .wordmark {
    color: var(--card-white);
    left: 50%;
    top: 50%;
    transform: translate(-50%, -50%);
  }
  .card-front .wordmark .mark-dot { background: var(--card-white); }
  .card-back .wordmark {
    color: var(--brand-red);
    right: 34px;
    top: 118px;
    font-size: 36px;
  }
  .card-back .wordmark .mark-dot { background: var(--brand-red); }
  .card-art {
    position: absolute;
    inset: 0;
  }
  .identity {
    position: absolute;
    left: 78px;
    top: 20px;
  }
  .identity .person-name {
    margin: 0;
    color: var(--brand-red);
    font-weight: 700;
    font-size: 18px;
    line-height: 1.1;
  }
  .identity .person-title {
    margin: 2px 0 0;
    color: var(--ink-soft);
    font-size: 13px;
  }
  .contact {
    position: absolute;
    left: 30px;
    top: 122px;
    color: var(--ink);
    font-size: 14px;
    line-height: 20px;
  }
  .contact p { margin: 0; }
  .contact .address { margin-bottom: 4px; }
  .contact .line {
    display: flex;
    align-items: center;
    gap: 10px;
  }
  .contact .icon {
    width: 11px;
    height: 11px;
    flex: none;
  }
  .contact .line.plain { padding-left: 21px; }
</style>
</head>
<body>
<main class="canvas">

  <section class="card card-front" aria-label="Business card front">
    <div class="wordmark"><span class="mark-dot"></span>VKT Consulting</div>
  </section>

  <section class="card card-back" aria-label="Business card back">
    <svg class="card-art" width="560" height="320" viewBox="0 0 560 320" aria-hidden="true">
      <polygon points="0,0 72,0 52,30 0,30" fill="var(--card-black)"/>
      <polygon points="36,30 58,0 72,0 50,30" fill="var(--card-white)"/>
      <polygon points="20,30 40,0 72,0 52,30" fill="var(--brand-red)"/>
      <polygon points="0,0 40,0 20,30 0,30" fill="var(--card-black)"/>
      <polygon points="0,232 292,232 276,262 0,262" fill="var(--card-black)"/>
      <polygon points="300,268 560,268 560,300 282,300" fill="var(--brand-red)"/>
    </svg>

    <div class="identity">
      <p class="person-name">Dana Melbrook</p>
      <p class="person-title">Principal</p>
    </div>

    <div class="contact">
      <p class="address">4820, Harbor Point Drive<br>Country Name, 123456.</p>
      <p class="line">
        <svg class="icon" viewBox="0 0 12 12" aria-hidden="true"><path d="M2 1 L4.5 1 L5.5 3.5 L4 4.5 Q5 7 7.5 8 L8.5 6.5 L11 7.5 L11 10 Q6 11 3 8 Q1 5.5 2 1Z" fill="var(--brand-red)"/></svg>
        044-555 210 487
      </p>
      <p class="line">
        <svg class="icon" viewBox="0 0 12 12" aria-hidden="true"><rect x="0.5" y="2" width="11" height="8" fill="var(--brand-red)"/><path d="M0.5 2 L6 6.5 L11.5 2" stroke="#fff" stroke-width="1" fill="none"/></svg>
        info@vktconsulting.com
      </p>
      <p class="line">
        <svg class="icon" viewBox="0 0 12 12" aria-hidden="true"><circle cx="6" cy="6" r="5.5" fill="var(--brand-red)"/><path d="M0.5 6 H11.5 M6 0.5 Q3 6 6 11.5 M6 0.5 Q9 6 6 11.5" stroke="#fff" stroke-width="0.8" fill="none"/></svg>
        www.vktconsulting.com
      </p>
    </div>

    <div class="wordmark"><span class="mark-dot"></span>VKT Consulting</div>
  </section>

</main>
</body>
</html>
```